Moravel Aesthetic Doctor

I require an elegant, luxurious looking business card for my aesthetic business. I am a doctor and that will set me aside from competitors. I am planning to provide home and spa based treatments to clients with high expectations. I have attached my logo.

```html
<!DOCTYPE html>
<html lang="en">
<head>
<meta charset="utf-8">
<title>Moravel Aesthetic Doctor – Business Card</title>
<link href="https://fonts.googleapis.com/css2?family=Open+Sans:wght@300;400;600&display=swap" rel="stylesheet">
<style>
  :root {
    --backdrop: #3a3a3c;
    --card: #1f2022;
    --card-front: #1a1b1d;
    --sky: #4fb3e8;
    --silver: #9aa1ab;
    --ink-light: #d8dadd;
    --ink-muted: #8d9096;
  }
  * { margin: 0; padding: 0; box-sizing: border-box; }
  html, body { width: 799px; height: 1200px; overflow: hidden; }
  body {
    background: var(--backdrop);
    font-family: "Open Sans", sans-serif;
    position: relative;
  }
  .card {
    position: absolute;
    left: 80px;
    width: 640px;
    height: 366px;
    overflow: hidden;
    border-radius: 3px;
    box-shadow: 0 10px 30px rgba(0,0,0,0.45);
  }
  .card--front { top: 150px; background: var(--card-front); }
  .card--back  { top: 690px; background: var(--card); }

  .front-mark {
    position: absolute;
    left: 0; right: 0; top: 0; bottom: 0;
    display: flex;
    align-items: center;
    justify-content: center;
    gap: 18px;
  }
  .front-mark__dot {
    width: 22px; height: 22px;
    border: 2px solid #6d7075;
    border-radius: 50%;
  }
  .front-mark__name {
    font-weight: 300;
    font-size: 46px;
    letter-spacing: 4px;
    color: #6d7075;
    text-transform: uppercase;
  }

  .card__waves { position: absolute; inset: 0; }

  .tagline {
    position: absolute;
    left: 38px; top: 22px;
    font-size: 13px;
    line-height: 16px;
    color: #ffffff;
    font-weight: 300;
  }

  .contacts {
    position: absolute;
    left: 38px; top: 206px;
    font-size: 14px;
    color: var(--ink-light);
    line-height: 24px;
  }
  .contacts__follow { display: flex; align-items: center; gap: 8px; margin-bottom: 4px; }
  .contacts__social { width: 13px; height: 13px; border: 1.5px solid var(--ink-light); border-radius: 50%; }
  .contacts__row { display: flex; align-items: center; gap: 12px; }
  .contacts__row svg { width: 12px; height: 12px; fill: var(--sky); flex: none; }

  .brand {
    position: absolute;
    left: 318px; top: 150px;
    display: flex;
    align-items: center;
    gap: 16px;
  }
  .brand__dot {
    width: 40px; height: 40px;
    border: 2px solid var(--silver);
    border-radius: 50%;
    flex: none;
  }
  .brand__name {
    color: var(--ink-light);
    font-weight: 300;
    text-transform: uppercase;
    line-height: 1;
  }
  .brand__name-main { display: block; font-size: 44px; letter-spacing: 3px; }
  .brand__name-sub { display: block; font-size: 17px; letter-spacing: 2.6px; margin-top: 6px; }

  .doctor {
    position: absolute;
    right: 40px; top: 258px;
    text-align: right;
  }
  .doctor__name { font-size: 21px; font-weight: 300; color: var(--ink-muted); }
  .doctor__letters { font-size: 10px; color: var(--sky); margin-top: 1px; }
  .doctor__diploma { font-size: 14px; color: var(--sky); line-height: 17px; margin-top: 4px; font-weight: 400; }
</style>
</head>
<body>

<section class="card card--front" aria-label="Card front">
  <div class="front-mark">
    <span class="front-mark__dot"></span>
    <span class="front-mark__name">Moravel</span>
  </div>
</section>

<section class="card card--back" aria-label="Card back">
  <svg class="card__waves" viewBox="0 0 640 366" preserveAspectRatio="none" aria-hidden="true">
    <path d="M0 0 H640 V180 C560 130 470 105 380 110 C250 118 170 70 0 62 Z" fill="var(--sky)"/>
    <path d="M0 62 C170 70 250 118 380 110 C470 105 560 130 640 180 V196 C560 146 470 122 380 126 C250 132 170 84 0 76 Z" fill="var(--silver)"/>
    <path d="M0 84 C160 92 240 138 380 132 C480 128 560 160 640 210 V214 C560 166 480 134 380 138 C240 144 160 98 0 90 Z" fill="#2c2d30"/>
  </svg>

  <p class="tagline">Home and Spa<br>Based Treatments</p>

  <div class="contacts">
    <div class="contacts__follow">Follow us on: <span class="contacts__social"></span><span class="contacts__social"></span></div>
    <div class="contacts__row">
      <svg viewBox="0 0 24 24"><path d="M6.6 10.8a15.5 15.5 0 0 0 6.6 6.6l2.2-2.2c.3-.3.7-.4 1-.2 1.1.4 2.3.6 3.6.6.6 0 1 .4 1 1V20c0 .6-.4 1-1 1A17 17 0 0 1 3 4c0-.6.4-1 1-1h3.5c.6 0 1 .4 1 1 0 1.3.2 2.5.6 3.6.1.3 0 .7-.2 1z"/></svg>
      <span>0800 457 319</span>
    </div>
    <div class="contacts__row">
      <svg viewBox="0 0 24 24"><path d="M2 5h20v14H2z M2 5l10 8 10-8" fill="none" stroke="var(--sky)" stroke-width="2.4"/></svg>
      <span>elise@moravel.co.nz</span>
    </div>
    <div class="contacts__row">
      <svg viewBox="0 0 24 24"><circle cx="12" cy="12" r="10" fill="none" stroke="var(--sky)" stroke-width="2.2"/><path d="M2 12h20M12 2c3 3 3 17 0 20M12 2c-3 3-3 17 0 20" fill="none" stroke="var(--sky)" stroke-width="1.8"/></svg>
      <span>www.moravel.co.nz</span>
    </div>
  </div>

  <div class="brand">
    <span class="brand__dot"></span>
    <span class="brand__name">
      <span class="brand__name-main">Moravel</span>
      <span class="brand__name-sub">Aesthetic Doctor</span>
    </span>
  </div>

  <div class="doctor">
    <p class="doctor__name">Dr Elise Varrow</p>
    <p class="doctor__letters">MRCPCH MD</p>
    <p class="doctor__diploma">Australasian Diploma of<br>Aesthetic Medicine</p>
  </div>
</section>

</body>
</html>
```